TOVR Restaurant Group Take Out Bags

We need bags designed for our restaurant group.

We are an upscale Chinese food restaurant. I have uploaded a few photos that our boss liked as inspiration. I also uploaded a few of our menus so you can see the aesthetic and our logos.

The main focus is TOVR Group, but please have all 5 logos somewhere on the bag.

Red, black and gold are the ideal color focus.

Two bag sizes, but they can have the same design.
Large: 15"W, 15"H, 8"D; Small: 10"W, 12"H, 6"D

```html
<!DOCTYPE html>
<html lang="en">
<head>
<meta charset="utf-8">
<title>TOVR Group Take Out Bag</title>
<link rel="stylesheet" href="https://fonts.googleapis.com/css2?family=Josefin+Sans:wght@400;600&display=swap">
<style>
  :root {
    --backdrop: #c9c9c9;
    --charcoal: #2e2e2e;
    --charcoal-deep: #262626;
    --doodle: #4a4a46;
    --cream: #f1e4b6;
    --cream-light: #f4ebc6;
    --ink: #2b2b2b;
    --red: #c8102e;
  }
  html, body {
    margin: 0;
    width: 1200px;
    height: 900px;
    overflow: hidden;
    background: var(--backdrop);
    font-family: "Josefin Sans", sans-serif;
  }
  .canvas {
    position: relative;
    width: 1200px;
    height: 900px;
  }
  .bag-face {
    position: absolute;
    left: 350px;
    top: 50px;
    width: 500px;
    height: 800px;
    overflow: hidden;
  }
  .doodle-pattern {
    position: absolute;
    inset: 0;
    background:
      radial-gradient(circle at 30% 20%, var(--doodle) 0, transparent 40%),
      radial-gradient(circle at 80% 75%, var(--doodle) 0, transparent 45%),
      linear-gradient(160deg, var(--charcoal), var(--charcoal-deep));
  }
  .eyelet {
    position: absolute;
    top: 22px;
    width: 10px;
    height: 10px;
    border: 4px solid var(--red);
    border-radius: 50%;
    background: var(--charcoal-deep);
  }
  .eyelet-left { left: 150px; }
  .eyelet-right { left: 330px; }
  .brand-patch {
    position: absolute;
    left: 80px;
    top: 205px;
    width: 345px;
    height: 365px;
    background: linear-gradient(180deg, var(--cream), var(--cream-light));
    clip-path: polygon(4% 3%, 40% 0, 62% 5%, 96% 1%, 92% 30%, 100% 40%, 94% 62%, 97% 98%, 55% 95%, 20% 100%, 3% 92%, 7% 60%, 0 35%);
  }
  .brand-lockup {
    position: absolute;
    left: 80px;
    width: 345px;
    top: 330px;
    text-align: center;
    color: var(--ink);
  }
  .brand-name {
    display: block;
    font-size: 72px;
    font-weight: 600;
    letter-spacing: 5px;
    padding-left: 5px;
    line-height: 1;
  }
  .brand-rule {
    display: block;
    width: 60px;
    height: 3px;
    margin: 14px auto 10px;
    background: var(--red);
  }
  .brand-sub {
    display: block;
    font-size: 15px;
    font-weight: 600;
    letter-spacing: 12px;
    padding-left: 12px;
  }
  .partner-band {
    position: absolute;
    left: 0;
    right: 0;
    top: 655px;
    height: 125px;
    background: var(--cream);
    display: flex;
    justify-content: center;
    align-items: center;
    gap: 20px;
    color: var(--ink);
  }
  .partner {
    display: flex;
    flex-direction: column;
    align-items: center;
    gap: 5px;
    text-align: center;
    white-space: nowrap;
  }
  .partner-name {
    font-size: 12px;
    font-weight: 600;
    letter-spacing: 0.5px;
  }
  .partner-tag {
    font-size: 7px;
    font-weight: 400;
    letter-spacing: 1.5px;
    text-transform: uppercase;
  }
</style>
</head>
<body>
<main class="canvas">
  <section class="bag-face">
    <div class="doodle-pattern" role="img" aria-label="Hand-drawn pattern of vegetables and herbs in grey on charcoal"></div>
    <span class="eyelet eyelet-left"></span>
    <span class="eyelet eyelet-right"></span>
    <div class="brand-patch"></div>
    <div class="brand-lockup">
      <span class="brand-name">TOVR</span>
      <span class="brand-rule"></span>
      <span class="brand-sub">GROUP</span>
    </div>
    <div class="partner-band">
      <div class="partner">
        <span class="partner-name">THE ATRIUM</span>
        <span class="partner-tag">Bar &amp; Kitchen</span>
      </div>
      <div class="partner">
        <span class="partner-name">JADE LANTERN</span>
        <span class="partner-tag">Fine Dining</span>
      </div>
      <div class="partner">
        <span class="partner-name">PEARL GARDEN</span>
        <span class="partner-tag">Tea House</span>
      </div>
      <div class="partner">
        <span class="partner-name">HARBOR HOUSE</span>
        <span class="partner-tag">Seafood</span>
      </div>
    </div>
  </section>
</main>
</body>
</html>
```